Harborview Estates Business Card for Apartment Buildings

Create business cards for resident managers who run apartment buildings. The audience is the public who are searching for apartment rentals, and current residents who live at the apartment building. Key design element will be incorporating the company logo, however, the logo cannot dominate. The building name and manager name are more important than the logo. Current business card design leaves little room for copy, so we may need to reduce the size on the current card to allow for more space for copy.

Target Market(s)

Adults 18-65 years of age, who are looking for an apartment rental, plus current residents who live at our apartment buildings.

Industry/Entity Type

Property Management

Contact Information for Business Card

A major design element will be use of the company logo. Important property and manager contact information must be part of the design. The size of the logo will need to be reduced to make room for building and manager contact copy.

Font styles to use
Sans Serif

Colors
3176b5
000000
959595
ffffff

Requirements
Must have
• 1) Incorporate the company logo.
• 2) Use the company colors (dark blue, black/grey, over white).
• 3) FEATURE THE BUILDING NAME
• 4) FEATURE THE MANAGER NAME
• 5) The company name is less important than BUILDING and MANAGER
• 6) Manager contact information
• **SEE ATTACHED CREATIVE BRIEF**
Nice to have
• 1) Back of card logo watermark
• 2) Ability to write notes on back of carfd
Should not have
• Avoid letting the company logo dominate the card, the building name and manager are more important than the company logo.

```html
<!DOCTYPE html>
<html lang="en">
<head>
<meta charset="utf-8">
<title>Harborview Estates Business Card</title>
<link href="https://fonts.googleapis.com/css2?family=Roboto:wght@400;500;700&family=Roboto+Condensed:wght@500;700&display=swap" rel="stylesheet">
<style>
  :root {
    --brand-blue: #1a6aa8;
    --ink: #3d3d3d;
    --rule: #2b2b2b;
    --paper: #f3f3f3;
    --backdrop: #2a2a2a;
    --muted: #959595;
  }
  * { margin: 0; padding: 0; box-sizing: border-box; }
  html, body {
    width: 1200px; height: 960px; overflow: hidden;
    background: var(--backdrop);
    font-family: "Roboto", Arial, sans-serif;
  }
  .card {
    position: absolute;
    width: 600px; height: 342px;
    background: var(--paper);
  }
  .card--front { left: 314px; top: 113px; }
  .card--back { left: 311px; top: 472px; }

  .brand {
    position: absolute;
    display: flex; align-items: center; gap: 10px;
    color: var(--brand-blue);
    font-family: "Roboto Condensed", Arial, sans-serif;
    font-weight: 700;
    white-space: nowrap;
  }
  .brand__mark { background: var(--brand-blue); flex: none; }
  .card--front .brand { right: 46px; top: 62px; font-size: 24px; }
  .card--front .brand__mark { width: 22px; height: 22px; }
  .card--back .brand { left: 50%; top: 50%; transform: translate(-50%, -50%); font-size: 44px; gap: 16px; }
  .card--back .brand__mark { width: 40px; height: 40px; }

  .name-tab {
    position: absolute; left: 0; top: 168px;
    width: 14px; height: 37px; background: var(--brand-blue);
  }
  .manager { position: absolute; left: 44px; top: 163px; }
  .manager__name {
    font-family: "Roboto Condensed", Arial, sans-serif;
    font-weight: 500; font-size: 24px; color: var(--brand-blue); line-height: 1.1;
  }
  .manager__title { font-weight: 500; font-size: 15px; color: var(--ink); margin-top: 2px; }

  .divider {
    position: absolute; left: 44px; top: 216px;
    width: 508px; height: 1px; background: var(--rule);
  }

  .property { position: absolute; left: 45px; top: 224px; color: var(--ink); }
  .property__name {
    font-family: "Roboto Condensed", Arial, sans-serif;
    font-weight: 500; font-size: 23px; color: var(--brand-blue); line-height: 1.2;
  }
  .property__address { font-size: 14.5px; line-height: 18px; }
  .property__web { font-size: 14.5px; margin-top: 7px; }

  .contact-list {
    position: absolute; right: 46px; top: 232px;
    list-style: none; color: var(--ink); font-size: 14.5px;
  }
  .contact-list li {
    display: flex; justify-content: flex-end; align-items: center;
    gap: 8px; height: 19.5px;
  }
  .contact-list svg { width: 13px; height: 13px; fill: var(--brand-blue); flex: none; }

  .footer-rule {
    position: absolute; left: 0; bottom: 14px; width: 100%;
    height: 1px; background: var(--muted);
  }
  .footer-band {
    position: absolute; left: 0; bottom: 0; width: 100%;
    height: 12px; background: var(--brand-blue);
  }
</style>
</head>
<body>
  <section class="card card--front" aria-label="Business card front">
    <div class="brand"><span class="brand__mark"></span>HARBORVIEW ESTATES</div>

    <div class="name-tab"></div>
    <div class="manager">
      <h1 class="manager__name">Marisol Quintero</h1>
      <p class="manager__title">Resident Manager</p>
    </div>

    <div class="divider"></div>

    <div class="property">
      <h2 class="property__name">Cedar Crest Apartments</h2>
      <p class="property__address">2145 Lindenwood Avenue<br>Bayfield, CA 90000</p>
      <p class="property__web">harborviewest.com</p>
    </div>

    <ul class="contact-list">
      <li>555-210-4417
        <svg viewBox="0 0 16 16" aria-label="Office phone"><path d="M3.6 1.2l2.3 2.6-1.3 2.1c.9 1.9 2.5 3.6 4.5 4.6l2.1-1.3 2.6 2.3-1.2 2.3C7 14 2 9 1.3 2.4z"/></svg>
      </li>
      <li>555-384-0962
        <svg viewBox="0 0 16 16" aria-label="Mobile phone"><path d="M4 0h8a1 1 0 011 1v14a1 1 0 01-1 1H4a1 1 0 01-1-1V1a1 1 0 011-1zm1 2v10h6V2zm3 11a1 1 0 100 2 1 1 0 000-2z" fill-rule="evenodd"/></svg>
      </li>
      <li>555-671-2038
        <svg viewBox="0 0 16 16" aria-label="Fax"><path d="M4 1h8v4H4zM1 6h14v6h-2v-3H3v3H1zM4 10h8v5H4z"/></svg>
      </li>
      <li>marisol@harborviewest.com
        <svg viewBox="0 0 16 16" aria-label="Email"><path d="M1 3h14v1L8 9 1 4zm0 3l7 5 7-5v7H1z"/></svg>
      </li>
    </ul>

    <div class="footer-rule"></div>
    <div class="footer-band"></div>
  </section>

  <section class="card card--back" aria-label="Business card back">
    <div class="brand"><span class="brand__mark"></span>HARBORVIEW ESTATES</div>
  </section>
</body>
</html>
```